Need a new company business card

I am looking for a new company business card. Front and back. With information on it as per below. Card should be professional. Yet clever. Simple. Modern design. Pim card, traditional size. OK with say, all black or all red backside.

Varnholt is an indie, bootstrapped magazine advancing the work of intersectional feminists busting their buts to create a just world through the power of enterprise and innovation.

Varnholt is the home and voice of entrepreneurial feminism and feminist innovators worldwide. Entrepreneurial feminists are people (of all genders) who see inequality as an innovation priority. They work to advance gender equity and/or who strive to integrate and practice feminist principles, pedagogy, values into their innovation and entrepreneurship work.
We are committed to this space being trans and queer inclusive, anti-racist, intersectional, brave, and safe. We welcome all allies. We value learning, edgy but civil discourse and integrative thinking skills.

Target Market(s)

feminists, business owners,

Industry/Entity Type

Publishing Company

Contact Information for Business Card

RD Tolliver
Founder/Publisher
4-237 Ashgrove Lane, Toronto, ON
M4T 2K8
publisher@varnholt.com
416-552-3019
www.varnholt.com

Font styles to use
Serif
Other font styles liked:
• Myriad Pro

Colors
ec1f27
000000
ffffff

Requirements
Must have
• logo
• use red, black white colours only.
Nice to have
• use the compass in pattern or creatively but not too busy please
Should not have
• Should not be too busy. Elegant.

```html
<!DOCTYPE html>
<html lang="en">
<head>
<meta charset="utf-8">
<title>Varnholt Business Card</title>
<link rel="stylesheet" href="https://fonts.googleapis.com/css2?family=Open+Sans:wght@400;700&family=Roboto:wght@400;500&family=PT+Serif:ital,wght@0,700;1,400&display=swap">
<style>
  :root {
    --brand-red: #ec1f27;
    --ink: #2b2b2b;
    --ink-soft: #4a4a4a;
    --paper: #f7f7f7;
    --backdrop: #e4e4e4;
    --band-dark: #333333;
    --rule: #d6d6d6;
  }
  * { box-sizing: border-box; margin: 0; padding: 0; }
  html, body {
    width: 1200px; height: 886px; overflow: hidden;
    background: var(--backdrop);
  }
  .canvas { position: relative; width: 1200px; height: 886px; }

  .card {
    position: absolute;
    width: 560px; height: 320px;
    box-shadow: 0 8px 22px rgba(0,0,0,.22);
    overflow: hidden;
  }

  /* Back side – solid red */
  .card-back {
    left: 50px; top: 120px;
    background: var(--brand-red);
    color: #fff;
  }
  .card-back .brand-lockup {
    position: absolute; right: 40px; bottom: 48px; text-align: left;
  }
  .brand-name {
    font-family: "Open Sans", sans-serif;
    font-weight: 700;
    letter-spacing: -1px;
    line-height: 1;
  }
  .card-back .brand-name { font-size: 50px; color: #fff; }
  .tagline {
    font-family: "PT Serif", serif;
    font-weight: 700;
    font-size: 7.5px;
    letter-spacing: .6px;
    text-transform: uppercase;
    margin-top: 4px;
    white-space: nowrap;
  }
  .tagline em { text-transform: none; font-style: italic; font-weight: 400; }
  .card-back .web {
    font-family: "Roboto", sans-serif;
    font-size: 13px; letter-spacing: 5px; margin-top: 8px;
  }

  /* Front side – white with swoosh */
  .card-front {
    left: 590px; top: 446px;
    background: var(--paper);
  }
  .card-front .brand-lockup {
    position: absolute; left: 44px; top: 112px;
  }
  .card-front .brand-name { font-size: 54px; color: var(--ink); }
  .card-front .tagline { color: var(--ink-soft); }

  .divider {
    position: absolute; left: 298px; top: 40px;
    width: 1px; height: 140px; background: var(--rule);
  }
  .contact {
    position: absolute; left: 318px; top: 40px;
    font-family: "Roboto", sans-serif; color: var(--ink-soft);
    font-size: 12.5px; line-height: 1.35;
  }
  .contact .person {
    font-weight: 500; font-size: 17px; color: var(--ink); letter-spacing: -.3px;
  }
  .contact .role { color: var(--brand-red); font-size: 15px; margin-bottom: 8px; }
  .contact .address { margin-bottom: 10px; }
  .contact ul { list-style: none; }
  .contact li { display: flex; align-items: center; gap: 8px; }
  .contact li svg { width: 11px; height: 11px; fill: var(--ink); flex: none; }

  .swoosh { position: absolute; left: 0; top: 0; width: 560px; height: 320px; }
</style>
</head>
<body>
<main class="canvas">

  <section class="card card-back" aria-label="Card back">
    <div class="brand-lockup">
      <div class="brand-name">Varnholt</div>
      <div class="tagline">Dispatches <em>for</em> equity-driven founders</div>
      <div class="web">www.varnholt.com</div>
    </div>
  </section>

  <section class="card card-front" aria-label="Card front">
    <svg class="swoosh" viewBox="0 0 560 320" aria-hidden="true">
      <path d="M0 320 C140 250 260 310 400 250 C470 220 530 195 560 180 L560 320 Z" fill="var(--band-dark)"/>
      <path d="M0 312 C140 232 260 292 400 232 C470 202 530 178 560 160 L560 168 C530 186 470 210 400 241 C260 300 140 242 0 318 Z" fill="var(--brand-red)"/>
    </svg>

    <div class="brand-lockup">
      <div class="brand-name">Varnholt</div>
      <div class="tagline">Dispatches <em>for</em> equity-driven founders</div>
    </div>

    <div class="divider"></div>

    <div class="contact">
      <div class="person">RD TOLLIVER</div>
      <div class="role">Founder/Publisher</div>
      <div class="address">4-237 Ashgrove Lane<br>Toronto, ON, M4T 2K8</div>
      <ul>
        <li>
          <svg viewBox="0 0 24 24"><path d="M6.6 10.8a15.1 15.1 0 0 0 6.6 6.6l2.2-2.2a1 1 0 0 1 1-.25 11.4 11.4 0 0 0 3.6.57 1 1 0 0 1 1 1V20a1 1 0 0 1-1 1A17 17 0 0 1 3 4a1 1 0 0 1 1-1h3.5a1 1 0 0 1 1 1c0 1.25.2 2.45.57 3.570a1 1 0 0 1-.25 1z"/></svg>
          416-552-3019
        </li>
        <li>
          <svg viewBox="0 0 24 24"><path d="M2 5h20v14H2z M2 5l10 8 10-8" fill="none" stroke="#2b2b2b" stroke-width="2.4"/></svg>
          publisher@varnholt.com
        </li>
        <li>
          <svg viewBox="0 0 24 24"><circle cx="12" cy="12" r="10"/></svg>
          www.varnholt.com
        </li>
      </ul>
    </div>
  </section>

</main>
</body>
</html>
```